Community Management Company in need of WordPress templates for website redesign

We are a community association management company providing services to homeowner associations (HOAs), condominium associations, cooperatives, municipal utility districts, luxury high-rises and large master-planned communities within the Real Estate category.

We are looking to do a refresh of our site with newly-designed pages that are compatible with WordPress and can be uploaded to a domain with little complications.

We are interested in first having a landing page designed based on a specific audience and call to actions as described in the design brief file attached to this design project and pasted below:
Design Brief for HavenStead Website Refresh

General Details:
Company Name: HavenStead
Business Location: Carrollton, TX – HQ
Current website: www.havenstead-example.com

Overview:

We are looking to for a refresh of our site with newly-designed pages that are compatible with WordPress and can be uploaded to a domain with little complications.

Our target audience / target market:
HOA and Association Board Members, Real Estate Builders & Developers, Residents and Homeowners, Vendors, Potential Business Partners

Project scope:
Create a landing page template with the target audience of HOA Board Members who are prospects of HavenStead
The goal of the landing page is to have them fill out the proposal form by having the page take them from our “why” message to our “how” and “what” messages so they are compelled to fill out the form. The new landing page needs to drive that behavior.
Our messages will include the following

Why messages:
• Because you deserve an exceptional community
• Because you and your residents deserve an exceptional lifestyle
• Because your community matters
• Because your residents matter
• Exceptional Community. Managed
• Exceptional Lifestyle. Delivered
How/What messages:

With over 25 years of experience, HavenStead provides exceptional community management solutions with the transparency and visibility your community deserves. Our fully integrated services are provided at competitive prices with the best people, best practices, and best cloud-based and mobile app technology.

Our team is made up of the industry’s leading experts equipped to answer your questions quickly. Our team includes: certified managers, degreed and certified accountants, experienced, multi-lingual customer service representatives, technology staff and industry executives. We perform industry leading best practices, on behalf of the communities we serve, ensuring you receive the highest level support, guidance and tools to assist in performing your fiduciary duties. With our proprietary, cloud-based and mobile app technology, pertinent community information is at your fingertips. You will be empowered to manage the business affairs of your community anytime, from any device, anywhere.

Our community management services include personalized onsite management, portfolio management, full-service community maintenance services, community management for builders and property developers, and Virtual CAM (Community Association Manager) management.

Our community communication services include cloud-based board, resident, closing, and attorney portals and mobile app technology, providing the transparency and visibility into the business affairs that your community deserves. In addition, we provide several communication tools to keep homeowners and residents informed via our community website, newsletter and event services.

HavenStead, one of the largest and fastest growing community management companies, is proud to provide exceptional services to hundreds of community associations from under 50 units to over 7,000 units in Arizona, California, Colorado, Florida, Georgia, Louisiana, Nevada, North Carolina, Oregon, Texas and Washington, including homeowner associations (HOAs), condominium associations, cooperatives, luxury high-rises, municipal utility districts and large master-planned communities.

Other page elements: additional content block/placeholders for:
• Link to Service description and technology pages
• Link to Mobile Apps page
• Request a proposal form fill content block
• Find an office form fill content block and link to local page upon completion of search via zip or state
• Contact us content block with information to include phone, email, fax, etc. and link to contact us landing page

Template Elements:
Files will also be uploaded including:
• Logo
• Colors
• Sales PPT for their reference

Please see attached design brief (file #4), logos (file #2&3), colors & branding standards (file #5) and a sales PPT deck (file #1) geared towards the audience for your reference.
Updates

Reason: I am extending the deadline by one week to give everyone a chance to provide updates based on the feedback and submissions. Thank you for all of your efforts. I look forward to seeing all of your designs.

Reason: Good day everyone, We are extending our deadline by one more week; so please continue to submit your designs and revisions. We look forward to seeing your work. Regards.

Thank you for all of your submissions.  I am in the process of getting votes tallied and should have some further information Tuesday of next week.

I am currently reviewing the votes and comments from the poll and will provide feedback within the next day; so please stay tuned.

We are conducting one more round of voting for the website refresh.  Once this is complete we will contact the finalists and make a selection shortly thereafter.  Thank you again for your participation.  Please stay tuned.

We are finalizing our 2nd poll and will request revisions, if appropriate.  Thank you.

Target Market(s)

HOA Board members per the design brief

Industry/Entity Type

Communication

Requirements
Must have
• focus on a landing page first; not the homepage design
Nice to have
• Please see design brief - File #4
Should not have
• home page elements for the time being.

```html
<!DOCTYPE html>
<html lang="en">
<head>
<meta charset="utf-8">
<title>HavenStead – Community Management</title>
<link href="https://fonts.googleapis.com/css2?family=Lato:wght@300;400;700&display=swap" rel="stylesheet">
<style>
:root{
  --green:#3b6a34;
  --green-dark:#2f5729;
  --teal:#1e6a80;
  --text:#222;
  --muted:#555;
  --band:#f7f7f7;
  --footer:#e4e4e4;
  --line:#e2e2e2;
}
*{box-sizing:border-box;margin:0;padding:0}
html,body{width:858px;height:1200px;overflow:hidden;background:#fff;font-family:'Lato',sans-serif;color:var(--text)}
.page{position:relative;width:858px;height:1200px}
.abs{position:absolute}
.brand{left:118px;top:16px;display:flex;align-items:center;gap:6px;font-size:22px;font-weight:700;color:var(--teal)}
.brand-dot{width:10px;height:10px;background:var(--green)}
.brand-sub{left:163px;top:43px;font-size:5px;color:var(--teal);letter-spacing:.3px}
.search{left:595px;top:25px;width:149px;height:22px;display:flex}
.search-field{flex:1;background:#eee;font-size:7.5px;color:#999;padding:8px 7px 0}
.search-btn{width:24px;background:var(--green);display:flex;align-items:center;justify-content:center}
.nav{left:0;top:63px;width:858px;height:34px;background:var(--green)}
.nav a{position:absolute;top:13px;font-size:8.5px;font-weight:700;color:#fff;text-decoration:none;white-space:nowrap}
.hero{left:0;top:97px;width:858px;height:340px;background:linear-gradient(180deg,#c9d8e6 0%,#e7e1d2 40%,#d8d0bd 70%,#5f7a45 100%)}
.hero-caption{left:96px;top:302px;width:674px;height:83px;background:rgba(60,60,60,.55);color:#fff;font-weight:700;font-size:19px;line-height:34px;text-align:center;padding-top:8px;text-transform:uppercase;letter-spacing:-.2px}
.arrow{top:254px;width:26px;height:27px;background:#fff;display:flex;align-items:center;justify-content:center}
.services h2{position:absolute;left:105px;top:482px;font-size:17px;font-weight:700}
.services p{position:absolute;left:105px;top:518px;width:380px;font-size:9.2px;line-height:13.8px}
.services ul{position:absolute;left:105px;top:572px;width:380px;list-style:none;font-size:9.2px;line-height:13.8px}
.services li{position:relative;padding-left:14px;margin-bottom:3.4px}
.services li::before{content:"";position:absolute;left:2px;top:4px;border-left:4px solid #999;border-top:3px solid transparent;border-bottom:3px solid transparent}
.btn-small{left:105px;top:668px;width:65px;height:21px;background:var(--green);color:#fff;font-size:7.5px;font-weight:700;text-align:center;line-height:21px}
.video{left:511px;top:484px;width:246px;height:184px;background:#2a2a2a;padding:5px 7px 7px}
.video-still{width:100%;height:100%;background:linear-gradient(180deg,#c9cdd2 0%,#e6ddcf 45%,#b7b2a8 100%);position:relative}
.band{left:0;top:716px;width:858px;height:220px;background:var(--band);border-top:1px solid var(--line)}
.quote{left:100px;top:762px;width:658px;text-align:center;font-size:21px;font-weight:300;line-height:28px;color:var(--muted)}
.btn-large{left:362px;top:850px;width:142px;height:34px;background:var(--green);color:#fff;font-size:12px;font-weight:700;text-align:center;line-height:34px}
.partners{left:96px;top:956px;width:662px;height:82px;border:1px solid var(--line);display:flex;align-items:center;background:#fff}
.partner{flex:1;text-align:center;font-size:14px;font-weight:700;color:#777;border-right:1px solid var(--line);height:54px;line-height:54px}
.partner:last-child{border-right:none}
.footer{left:0;top:1081px;width:858px;height:109px;background:var(--footer)}
.footer-strip{left:0;top:1190px;width:858px;height:10px;background:var(--green)}
.footer-links{left:118px;top:1122px;font-size:8.5px;color:#222;white-space:nowrap;word-spacing:1px}
.copyright{left:118px;top:1152px;font-size:8.5px;color:#222}
.social{top:1123px;width:22px;height:22px;background:#3a5a97}
</style>
</head>
<body>
<div class="page">
  <header>
    <div class="abs brand"><span class="brand-dot"></span>HavenStead</div>
    <div class="abs brand-sub">powered by HavenLink</div>
    <div class="abs search">
      <div class="search-field">SEARCH</div>
      <div class="search-btn"><svg width="11" height="11" viewBox="0 0 11 11"><circle cx="4.5" cy="4.5" r="3.3" fill="none" stroke="#fff" stroke-width="1.6"/><line x1="7" y1="7" x2="10" y2="10" stroke="#fff" stroke-width="1.8"/></svg></div>
    </div>
  </header>
  <nav class="abs nav">
    <a style="left:118px">HOME</a>
    <a style="left:177px">REQUEST A PROPOSAL</a>
    <a style="left:305px">ABOUT US</a>
    <a style="left:386px">SERVICES</a>
    <a style="left:464px">JOIN OUR TEAM</a>
    <a style="left:566px">BLOG</a>
    <a style="left:622px">CONTACT US</a>
  </nav>

  <section>
    <div class="abs hero" role="img" aria-label="Photo of a large cream house with dark tiled roof, columns, garden and fountain"></div>
    <div class="abs arrow" style="left:0"><svg width="10" height="12" viewBox="0 0 10 12"><polyline points="7,1 2,6 7,11" fill="none" stroke="var(--green)" stroke-width="2.4"/></svg></div>
    <div class="abs arrow" style="left:832px"><svg width="10" height="12" viewBox="0 0 10 12"><polyline points="3,1 8,6 3,11" fill="none" stroke="var(--green)" stroke-width="2.4"/></svg></div>
    <div class="abs hero-caption">We offer exceptional community management solutions with<br>the best people, best practices, and best technology</div>
  </section>

  <section class="services">
    <h2>Our Services</h2>
    <p>Lorem ipsum dolor sit amet, consectetur adipiscing elit. Integer posuere erat a ante venenatis dapibus posuere velit aliquet. Cras justo odio, dapibus ac facilisis in, egestas eget quam. Curabitur blandit tempus porttitor.</p>
    <ul>
      <li>Cras justo odio, dapibus ac facilisis in, egestas eget quam.</li>
      <li>Nullam quis risus eget urna mollis ornare vel eu leo.</li>
      <li>Praesent commodo cursus magna, vel scelerisque nisl consectetur et.</li>
      <li>Curabitur blandit tempus porttitor. Lorem ipsum dolor sit amet, consectetur adipiscing elit.</li>
    </ul>
    <div class="abs btn-small">Read more</div>
    <div class="abs video">
      <div class="video-still" role="img" aria-label="Video still of a sunset over the sea">
        <svg class="abs" style="left:94px;top:64px" width="46" height="46" viewBox="0 0 46 46"><circle cx="23" cy="23" r="20" fill="rgba(255,255,255,.25)" stroke="var(--green-dark)" stroke-width="3.5"/><polygon points="17,12 34,23 17,34" fill="var(--green-dark)"/></svg>
      </div>
    </div>
  </section>

  <section>
    <div class="abs band"></div>
    <p class="abs quote">Vestibulum id ligula porta felis euismod semper. Donec sed odio dui. Cum sociis natoque penatibus et magnis dis parturient montes.</p>
    <div class="abs btn-large">Request information</div>
  </section>

  <section class="abs partners">
    <div class="partner">Greenleaf Co</div>
    <div class="partner">Waypoint Guide</div>
    <div class="partner">Homeward Realty</div>
    <div class="partner">Journey Partners</div>
  </section>

  <footer>
    <div class="abs footer"></div>
    <div class="abs footer-links">HOME &nbsp;| &nbsp;REQUEST A PROPOSAL &nbsp;| &nbsp;ABOUT US &nbsp;| &nbsp;SERVICES &nbsp;| &nbsp;JOIN OUR TEAM &nbsp;| &nbsp;BLOG &nbsp;| &nbsp;CONTACT US</div>
    <div class="abs copyright">COPYRIGHT 2014 &nbsp;HAVENSTEAD &nbsp;| &nbsp;ALL RIGHTS RESERVED.</div>
    <div class="abs social" style="left:661px" aria-label="Social link"></div>
    <div class="abs social" style="left:687px;background:#4aa3d8" aria-label="Social link"></div>
    <div class="abs social" style="left:713px;background:#2a6fa8" aria-label="Social link"></div>
    <div class="abs footer-strip"></div>
  </footer>
</div>
</body>
</html>
```